Holistic/ Sports Psychologist needs flyer design

I need a flyer designed that catches the attention of potential customers - (parents of young athletes and athletes) who may be looking for psychological services. I have a logo and all the relevant info for the flyer but would like someone to take it and make it look creative, fun, fresh and attention getting for high school and college athletes. The colors used can be from my logo design which represents my holistic approach.
Target Market(s)
high school and collegiate athletes
Industry/Entity Type
sports psychology
Requirements
Must have
- Info I put on the flyer with my logo and please add some graphics and color based on my logo

```html
<!DOCTYPE html>
<html lang="en">
<head>
<meta charset="utf-8">
<title>Holistic Psychology and Sports Psychology Consulting</title>
<link rel="stylesheet" href="https://fonts.googleapis.com/css2?family=Itim&family=Poppins:wght@400;600;700&family=Questrial&display=swap">
<style>
:root{
  --blue:#2f5e9e;
  --blue-deep:#2a5690;
  --green:#8cc55a;
  --green-soft:#8fbf7a;
  --card-blue:#3a6ea5;
  --ink:#1d1d1d;
  --white:#ffffff;
  --backdrop:#e9eaec;
}
*{margin:0;padding:0;box-sizing:border-box}
html,body{width:1035px;height:1200px;overflow:hidden;background:var(--backdrop)}
.stage{position:relative;width:1035px;height:1200px}
.flyer{position:absolute;left:54px;top:0;width:1010px;height:1308px;background:var(--white);
  transform:scale(.9174);transform-origin:top left;overflow:hidden;font-family:"Poppins",sans-serif;color:var(--ink)}
.abs{position:absolute}
.art{position:absolute;left:0;top:0}

.brand{left:58px;top:56px;display:flex;align-items:center;gap:14px}
.brand-mark{width:112px;height:112px;border-radius:50%;border:4px solid var(--blue);background:#eef3f8}
.brand-name{font-family:"Itim",cursive;font-weight:400;font-size:29px;color:var(--blue);margin-top:-18px}
.brand-bar{left:175px;top:122px;width:344px;height:24px;background:var(--green)}

.headline{left:58px;top:192px;font-family:"Itim",cursive;font-weight:400;color:var(--blue);font-size:49px;line-height:54px}
.headline-accent{left:54px;top:290px;font-family:"Itim",cursive;font-weight:400;color:var(--green);font-size:104px;line-height:120px}

.ways{left:60px;top:488px;font-family:"Questrial",sans-serif;font-weight:400;font-size:19.5px;letter-spacing:2.3px;line-height:25px}
.ways .l1{color:var(--blue)} .ways .l2{color:var(--green)}

.service{position:absolute;left:60px;width:500px;height:72px}
.service-icon{position:absolute;left:0;top:0;width:72px;height:72px}
.service-title{position:absolute;left:87px;top:-6px;font-family:"Questrial",sans-serif;font-weight:400;font-size:18.5px;line-height:22px;letter-spacing:1.6px;color:var(--blue);white-space:nowrap}
.service-text{position:absolute;left:88px;top:22px;width:410px;font-size:14.6px;line-height:18px;white-space:nowrap}

.bio-card{left:630px;top:632px;width:321px;height:453px;border-radius:24px;
  background:linear-gradient(180deg,var(--green-soft) 0%,#6f9f95 45%,var(--card-blue) 100%)}
.portrait{left:672px;top:499px;width:236px;height:236px;border-radius:50%;border:5px solid var(--white);
  background:radial-gradient(circle at 50% 45%,#c9a895 0%,#6b5a57 45%,#3f4d6a 100%)}
.bio{left:653px;top:758px;width:290px;color:var(--white);font-size:14.6px;line-height:17.8px;white-space:nowrap}
.bio strong{font-weight:700;font-size:17.5px}
.bio .spec{margin-top:18px}
.bio .spec b{font-weight:600}

.telehealth{left:220px;top:1106px;width:570px;height:73px;background:var(--blue);border-radius:6px;text-align:center;padding-top:7px}
.telehealth .main{color:var(--white);font-weight:700;font-size:23px;line-height:28px}
.telehealth .sub{color:var(--green);font-size:21.5px;line-height:28px}

.contact{color:var(--white);display:flex;align-items:center;gap:8px}
.contact svg{flex:none}
.address{left:60px;top:1214px;font-size:19.5px;line-height:20px}
.phone{left:414px;top:1222px;font-size:24px;font-weight:700}
.web{left:662px;top:1220px;font-size:21px}
</style>
</head>
<body>
<main class="stage">
  <article class="flyer">
    <svg class="art" width="1010" height="1308" viewBox="0 0 1010 1308">
      <defs>
        <linearGradient id="footerFill" x1="0" y1="0" x2="0" y2="1">
          <stop offset="0" stop-color="#88bb7c"/><stop offset="1" stop-color="#76a89c"/>
        </linearGradient>
        <linearGradient id="photoFill" x1="0" y1="0" x2="1" y2="1">
          <stop offset="0" stop-color="#e9e6df"/><stop offset=".5" stop-color="#c9a58f"/><stop offset="1" stop-color="#3b3f4a"/>
        </linearGradient>
      </defs>
      <path d="M0 396 C150 450 340 470 520 440 C590 428 640 410 680 392 C640 420 590 438 520 452 C340 482 150 470 0 432 Z" fill="var(--blue-deep)"/>
      <path d="M740 0 C650 60 585 170 600 280 C612 360 660 415 705 445 C650 400 618 330 618 260 C618 150 680 60 760 0 Z" fill="var(--green)"/>
      <circle cx="865" cy="239" r="250" fill="url(#photoFill)" role="img" aria-label="Photo of smiling young athletes holding basketballs in a gym"/>
      <path d="M0 1222 C250 1170 760 1160 1010 1222 L1010 1308 L0 1308 Z" fill="url(#footerFill)"/>
    </svg>

    <div class="abs brand-bar"></div>
    <div class="abs brand">
      <div class="brand-mark"></div>
      <span class="brand-name">Dr. Elena Whitford</span>
    </div>

    <h1 class="abs headline">Holistic Psychology and<br>Sports Psychology</h1>
    <div class="abs headline-accent">Consulting</div>

    <h2 class="abs ways"><span class="l1">WAYS TO IMPROVE ATHLETIC PERFORMANCE</span><br><span class="l2">USING SPORTS AND HOLISTIC PSYCHOLOGY</span></h2>

    <section class="service" style="top:560px">
      <svg class="service-icon" viewBox="0 0 72 72"><circle cx="36" cy="36" r="34" fill="none" stroke="var(--blue)" stroke-width="2.5"/><circle cx="36" cy="26" r="9" fill="none" stroke="var(--green)" stroke-width="3"/><path d="M18 46 h10 l8 4 h14 l-6 6 h-26z" fill="var(--blue)"/></svg>
      <h3 class="service-title">Mental Skills Training</h3>
      <p class="service-text">Ex visualization, goal-setting, motivation,<br>self- talk, mindset, concentration techniques</p>
    </section>

    <section class="service" style="top:656px">
      <svg class="service-icon" viewBox="0 0 72 72"><circle cx="36" cy="36" r="34" fill="none" stroke="var(--blue)" stroke-width="2.5"/><rect x="19" y="40" width="6" height="12" fill="var(--blue)"/><rect x="28" y="34" width="6" height="18" fill="var(--blue)"/><rect x="37" y="28" width="6" height="24" fill="var(--blue)"/><rect x="46" y="22" width="6" height="30" fill="var(--blue)"/><path d="M18 32 L30 24 L38 26 L52 14" fill="none" stroke="var(--green)" stroke-width="3"/></svg>
      <h3 class="service-title">Performance Enhancement</h3>
      <p class="service-text">eliminate psychological barriers that are hindering<br>performance such as self- doubt, perfectionism,<br>fear of failure, and burnout</p>
    </section>

    <section class="service" style="top:763px">
      <svg class="service-icon" viewBox="0 0 72 72"><circle cx="36" cy="36" r="34" fill="none" stroke="var(--blue)" stroke-width="2.5"/><path d="M26 54 V44 c-6-4-6-14 2-18 c6-3 16-1 18 6 l4 8 h-4 v8 h-6 v6z" fill="var(--blue)"/><path d="M37 26 c-6-2-8-8-6-12 c5 1 8 5 6 12 c2-7 6-10 10-9 c0 5-4 9-10 9z" fill="var(--green)"/></svg>
      <h3 class="service-title">Mental Health</h3>
      <p class="service-text">anxiety and stress management by using relaxation<br>techniques, breathwork, and mindfulness practices</p>
    </section>

    <section class="service" style="top:862px">
      <svg class="service-icon" viewBox="0 0 72 72"><circle cx="36" cy="36" r="34" fill="none" stroke="var(--blue)" stroke-width="2.5"/><circle cx="30" cy="18" r="4" fill="var(--green)"/><rect x="42" y="18" width="10" height="14" rx="2" fill="var(--green)"/><path d="M14 48 h12 l10 4 h16 l8-6 v6 l-10 8 h-24 l-12-4z" fill="var(--blue)"/></svg>
      <h3 class="service-title">Injury Recovery Support</h3>
      <p class="service-text">assist athletes in maintaining resilience &amp; positive<br>mental attitude during rehabilitation as well as<br>processing emotions relating to any potential<br>trauma caused by the injury or life transitions<br>resulting from it.</p>
    </section>

    <section class="service" style="top:1000px">
      <svg class="service-icon" viewBox="0 0 72 72"><circle cx="36" cy="36" r="34" fill="none" stroke="var(--blue)" stroke-width="2.5"/><circle cx="36" cy="26" r="5" fill="var(--blue)"/><path d="M20 36 l10 4 h12 l10-4 l2 3 l-10 5 v6 l8 4 h-32 l8-4 v-6 l-10-5z" fill="var(--blue)"/><circle cx="20" cy="18" r="3.5" fill="var(--green)"/><circle cx="52" cy="18" r="3.5" fill="none" stroke="var(--green)" stroke-width="2.5"/></svg>
      <h3 class="service-title">Burnout prevention</h3>
      <p class="service-text">teach athletes how to have balance in sports and<br>life so they can experience longevity in their sports<br>as well as overall optimal health and well-being.</p>
    </section>

    <div class="abs bio-card"></div>
    <div class="abs portrait" role="img" aria-label="Portrait photo of the psychologist"></div>
    <div class="abs bio">
      <p><strong>Dr. Elena Whitford</strong><br>is a licensed psychologist. She<br>understands the unique experiences<br>of athletes due to her background as<br>an All-American swimmer, collegiate<br>and age group swim coach, parent<br>of a collegiate/professional athlete,<br>and sports psychology researcher.<br>She works with athletes to optimize<br>performance and overall well-being.</p>
      <p class="spec"><b>Her specializations include:</b><br>performance anxiety, mental<br>performance, stress management,<br>anxiety, depressions, trauma, life<br>transitions, relationship issues, injury,<br>and sleep</p>
    </div>

    <div class="abs telehealth">
      <p class="main">All services are provided online via telehealth</p>
      <p class="sub">Sessions are 30 or 55 minutes.</p>
    </div>

    <div class="abs contact address">
      <svg width="18" height="22" viewBox="0 0 18 22"><path d="M9 1a7 7 0 0 1 7 7c0 5-7 13-7 13S2 13 2 8a7 7 0 0 1 7-7z" fill="var(--blue)"/><circle cx="9" cy="8" r="2.6" fill="var(--white)"/></svg>
      <span>2250 Harbor Lane #104<br>Seaview Bay, FL 32099</span>
    </div>
    <div class="abs contact phone">
      <svg width="18" height="18" viewBox="0 0 18 18"><circle cx="9" cy="9" r="8.5" fill="var(--blue)"/><path d="M6 4.5l2 2-1 1.2c.6 1.4 1.6 2.4 3 3l1.2-1 2 2-1.3 1.6C8.5 13 5 9.5 4.7 5.8z" fill="var(--white)"/></svg>
      <span>555-014-2288</span>
    </div>
    <div class="abs contact web">
      <svg width="18" height="18" viewBox="0 0 18 18"><circle cx="9" cy="9" r="8.5" fill="var(--blue)"/><g fill="none" stroke="var(--white)" stroke-width="1.1"><circle cx="9" cy="9" r="5.5"/><ellipse cx="9" cy="9" rx="2.4" ry="5.5"/><path d="M3.5 9h11"/></g></svg>
      <span>www.drelenawhitford.com</span>
    </div>
  </article>
</main>
</body>
</html>
```